Vennekamp.dk - FellowCup

I need a design for a WordPress site that serves to inform and present the national golfchampionship for colleagues in Denmark. The sites need to be visual stuninng or big, and it doesnt have a lot of pages. Maybe 5-6 regular text pages and not a lot of navigation. It should be a simple and powerfull site.

The sites need to present and sell the tournament, and have a clear call to action button "Sign up" (Tilmeld) and resultscoring.

If you can make a logo and visual ID for the tournament as well that would be a bonus.

Target Market(s)

Golfers

Logo Text

Vennekamp

Number of Pages Required

3 page

Requirements
Must have
• A frontpage
• Button 1 - Tilmeld (danish for sign up)
• Button 2 - Resultater (results)
Nice to have
• Logo
• A style we can use offline as well

```html
<!DOCTYPE html>
<html lang="da">
<head>
<meta charset="utf-8">
<title>Vennekamp 2015</title>
<link href="https://fonts.googleapis.com/css2?family=Roboto:wght@300;400;500;700&display=swap" rel="stylesheet">
<style>
:root{
  --blue:#0a72b8; --blue-dark:#0b5a94; --navy:#0d2c53; --green:#0b8551; --gold:#d1a300;
  --red:#b5202e; --grey-bg:#e9e9e9; --grey-side:#ececec; --text:#333; --muted:#666;
  --link:#0b8551; --footer:#3a3a3a;
}
*{box-sizing:border-box;margin:0;padding:0}
html,body{width:706px;height:1200px;overflow:hidden}
body{font-family:"Roboto",Arial,sans-serif;color:var(--text);background:#fff;position:relative;font-size:6.4px;line-height:1.45}
.wrap{width:550px;margin-left:78px;position:relative}
.header{height:67px;position:relative}
.brand{position:absolute;left:78px;top:14px;display:flex;align-items:center;gap:6px}
.brand-dot{width:34px;height:34px;border-radius:50%;background:var(--blue)}
.brand-name{font-weight:700;font-size:10px;line-height:1.05;letter-spacing:.5px;color:#222;text-transform:uppercase}
.search{position:absolute;left:524px;top:14px;width:104px;height:21px;border:1px solid #ccc;font-size:5.5px;color:#999;padding:6px 8px}
.search svg{position:absolute;right:6px;top:6px}
.toplinks{position:absolute;right:78px;top:48px;font-size:5.4px;color:#555;white-space:nowrap}
.toplinks span{margin:0 2px}
.nav{height:23px;background:var(--blue)}
.nav ul{list-style:none;display:flex;width:550px;margin-left:78px;height:23px}
.nav li{flex:1;color:#fff;font-size:6.6px;font-weight:500;text-transform:uppercase;display:flex;align-items:center;justify-content:center;border-right:1px solid var(--blue-dark)}
.nav li:first-child{background:var(--blue-dark);flex:.9}
.subbar{height:24px;background:var(--grey-bg);font-size:5.6px;color:#555;padding:7px 0 0 104px}
.hero{height:212px;background:linear-gradient(100deg,#dfe6ec 0%,#c9d6df 45%,#7aa04c 75%,#4f8a2f 100%);position:relative}
.hero h2{position:absolute;left:78px;top:40px;font-weight:300;font-size:13px;line-height:1.35;color:#555}
.dots{position:absolute;left:332px;top:191px;display:flex;gap:4px;background:rgba(0,0,0,.35);padding:3px 5px;border-radius:6px}
.dots i{width:4px;height:4px;border-radius:50%;background:#fff;display:block}
.cta{display:flex;height:36px}
.cta a{flex:1;color:#fff;font-weight:700;font-size:12px;text-decoration:none;display:flex;align-items:center;justify-content:center;gap:5px}
.cta .signup{background:var(--green);flex:0 0 353px}
.cta .results{background:var(--gold)}
.body{display:flex;gap:13px;margin-top:14px}
.side{width:131px;flex:none}
.side-head{background:var(--navy);color:#fff;font-size:8px;padding:6px 8px;height:24px}
.side-list{list-style:none;background:var(--grey-side)}
.side-list li{font-size:5.6px;padding:5px 0 5px 9px;border-bottom:1px solid #fff;height:19px}
.side-list li::before{content:"•";margin-right:4px;color:#888}
.contact{margin-top:13px;background:var(--grey-side);padding-bottom:10px}
.contact .person{margin:8px 9px 4px;height:59px;background:linear-gradient(135deg,#b88a6a,#6a5a52 60%,#2c2c34)}
.contact p{font-size:5.5px;padding:0 9px;line-height:1.6}
.contact .name{font-size:7px;color:#333}
.partners{margin-top:18px;font-size:4.8px}
.partner-mark{display:block;color:var(--navy);font-size:9px;font-weight:500;margin:3px 0 10px}
.partner-badge{width:38px;height:38px;border-radius:50%;background:#d7dde6;margin:0 0 3px 14px}
.main{width:406px;flex:none}
.finder{background:var(--grey-bg);height:34px;display:flex;align-items:center;padding:0 6px;gap:3px}
.finder label{font-size:6px;line-height:1.2;width:70px;color:#333}
.finder .field{background:#fff;height:18px;width:98px;font-size:5.4px;color:#888;padding:6px 8px;position:relative}
.finder .field.sel::after{content:"⌄";position:absolute;right:6px;top:3px;font-size:7px}
.finder .go{background:var(--navy);color:#fff;font-size:6px;height:18px;width:26px;display:flex;align-items:center;justify-content:center;font-weight:500}
h1{color:var(--red);font-weight:400;font-size:14.5px;margin:16px 0 7px}
.sub{font-size:6.4px;margin-bottom:6px}
.feature{display:flex;background:var(--grey-bg);height:140px}
.video{width:210px;height:140px;flex:none;background:linear-gradient(180deg,#8fb0d2 0%,#c8d6e3 45%,#8a9a6a 60%,#5f7846 100%);position:relative}
.play{position:absolute;left:95px;top:60px}
.info{padding:10px 18px}
.info .btn{display:inline-flex;align-items:center;gap:4px;background:var(--gold);color:#fff;font-weight:500;font-size:10px;padding:4px 8px;margin-bottom:6px}
.info h4{font-weight:400;font-size:6px;margin-bottom:4px}
.info p{font-size:5.3px;color:var(--muted);margin-bottom:6px}
.info ul{list-style:none}
.info li{font-size:5.1px;color:var(--link);line-height:1.85}
.info li::before{content:"• "}
.lead{color:var(--blue);font-size:7.4px;margin:10px 0 11px}
.facts p{font-size:6px;margin-bottom:5px}
.facts b{font-weight:400}
.facts span{color:var(--muted)}
.copy p{font-size:6px;line-height:1.6;color:var(--muted);margin-bottom:9px}
.copy p.dark{color:#333}
.copy h3{font-weight:500;font-size:6.2px;color:#333;margin:13px 0 6px}
.footer{position:absolute;left:0;top:1153px;width:706px;height:47px;background:var(--footer);color:#ddd}
.footer .fbrand{position:absolute;left:80px;top:14px;display:flex;align-items:center;gap:4px;color:#bbb;font-size:5.4px;font-weight:700;text-transform:uppercase;line-height:1.1}
.footer .fbrand i{width:18px;height:18px;border-radius:50%;background:#888;display:block}
.footer .links{position:absolute;left:161px;top:11px;font-size:5.2px}
.footer .copyr{position:absolute;left:161px;top:29px;font-size:5px;color:#bbb}
.footer .soc{position:absolute;left:562px;top:14px;display:flex;gap:4px;align-items:center}
.footer .soc i{width:14px;height:14px;border-radius:50%;background:var(--blue);display:block}
.footer .soc .partner-round{width:22px;height:22px;background:#888;margin-left:12px}
</style>
</head>
<body>
<header class="header">
  <div class="brand"><span class="brand-dot"></span><span class="brand-name">Nordlys<br>Idræts-<br>forbund</span></div>
  <div class="search">Search
    <svg width="8" height="8" viewBox="0 0 10 10"><circle cx="4" cy="4" r="3" fill="none" stroke="#777" stroke-width="1.3"/><line x1="6.3" y1="6.3" x2="9" y2="9" stroke="#777" stroke-width="1.3"/></svg>
  </div>
  <div class="toplinks">Om Nordlys Idrætsforbund <span>|</span> Bliv medlem <span>|</span> Magasinet NORDLYS <span>|</span> Find forening <span>|</span> Pressecenter <span>|</span> Find person <span>|</span> Min side</div>
</header>
<nav class="nav"><ul><li>Idraet og motion</li><li>Arrangementer og staevner</li><li>Sundhed pa arbejdspladsen</li><li>Foreningsnet</li></ul></nav>
<div class="subbar">Find stævner og arrangementer f.eks. Nordlys Open, Kyst og Skov Stafetten, Vild Mandedag og foreningsarrangementer</div>
<section class="hero" role="img" aria-label="Golfspiller i fuldt sving på en grøn bakke under lys himmel">
  <h2>Pellentesque blandit lacus<br>eget nunc faucibus et tincidunt</h2>
  <div class="dots"><i></i><i></i><i></i><i></i></div>
</section>
<div class="cta">
  <a class="signup" href="#"><svg width="10" height="10" viewBox="0 0 10 10"><rect x="1" y="2" width="7" height="7" fill="none" stroke="#fff" stroke-width="1.2"/><line x1="4" y1="6" x2="9" y2="1" stroke="#fff" stroke-width="1.5"/></svg>Tilmeld</a>
  <a class="results" href="#"><svg width="9" height="10" viewBox="0 0 9 10"><rect x="1" y="1" width="7" height="8" fill="none" stroke="#fff" stroke-width="1.2"/><line x1="2.5" y1="4" x2="6.5" y2="4" stroke="#fff"/><line x1="2.5" y1="6" x2="6.5" y2="6" stroke="#fff"/></svg>Resultater</a>
</div>
<div class="wrap body">
  <aside class="side">
    <div class="side-head">Arrangementer og stævner</div>
    <ul class="side-list">
      <li>Nordlys Open</li><li>Kyst og Skov Stafetten</li><li>Vild Mandedag</li><li>Fælles Motionsdag 2015</li><li>Adventurerace</li><li>Vennekamp</li><li>Vennebold</li><li>Fjord Cup Fodbold</li><li>Fjord Cup Høvdingebold</li><li>Internetskydning</li><li>Gokart</li><li>Arkiv</li>
    </ul>
    <div class="contact">
      <div class="side-head">Kontakt</div>
      <div class="person" role="img" aria-label="Portræt af kontaktperson foran murstensvæg"></div>
      <p class="name">Peter Holmgaard</p>
      <p>Generalsekretær<br>Tlf: 40 00 11 22<br>Mail: ph@nordlysidraet.dk</p>
    </div>
    <div class="partners">I samarbejde med:
      <span class="partner-mark">NORDISK GOLFRÅD</span>
      <div class="partner-badge"></div>
      <span class="partner-mark" style="font-size:12px">Havbo Rejser</span>
    </div>
  </aside>
  <main class="main">
    <div class="finder"><label>Find arrangement/ stævne</label><div class="field">Søgeord</div><div class="field sel">Vaelg kommune</div><div class="field sel">Vaelg tidspunkt</div><div class="go">SOG</div></div>
    <h1>Vennekamp 2015</h1>
    <p class="sub">Se video fra Vennekamp finalen 2011</p>
    <div class="feature">
      <div class="video" role="img" aria-label="To golfspillere med golfvogne på en bane">
        <svg class="play" width="20" height="20" viewBox="0 0 20 20"><circle cx="10" cy="10" r="10" fill="#fff"/><circle cx="10" cy="10" r="8" fill="#1e88d0"/><path d="M8 6l6 4-6 4z" fill="#fff"/></svg>
      </div>
      <div class="info">
        <span class="btn"><svg width="8" height="9" viewBox="0 0 9 10"><rect x="1" y="1" width="7" height="8" fill="none" stroke="#fff" stroke-width="1.2"/></svg>Resultater</span>
        <h4>Mere information</h4>
        <p>Se resultaterne fra finalen her! NB: Klik på holdnavnet for en mere detaljeret score.</p>
        <ul><li>Puljer (PDF, 203 KB)</li><li>Turneringsplan (PDF, 339 KB)</li><li>Turneringsbetingelser (PDF, 84 KB)</li><li>Holdkaptajner (PDF, 254 KB)</li><li>7_8_handicaptabel (PDF, 102 KB)</li><li>Ofte stillede spørgsmål (PDF, 89 KB)</li></ul>
      </div>
    </div>
    <p class="lead">Danmarks sjoveste kollegaturnering i golf. Spil mod andre spillere på nye baner.</p>
    <div class="facts">
      <p><b>Tidspunkt :</b> <span>1. maj 2015 kl. 07:00 - 18. sep 2015 kl. 21:30</span></p>
      <p><b>Kontakt :</b> <span>Karin Dahl, Tlf. 65 00 12 34</span></p>
      <p><b>Tilmeldingsfrist :</b> <span>27. april 2015</span></p>
    </div>
    <div class="copy">
      <p class="dark" style="margin-top:18px">Turneringen afvikles i 2015 for 8. gang.<br>Finalestævnet er i år på Egebjerg Golfklubs bane på Fyn.</p>
      <p class="dark">Vær med, og vind rejsegavekort for hele holdet på op til kr. 22.000,- som 1. præmie, dog max. kr. 5.500,- pr. deltager, jf. amatørbestemmelserne.</p>
      <p style="margin-top:16px"><b style="color:#333;font-weight:500">Pris :</b> Kr. 500,- pr. hold.</p>
      <p><b style="color:#333;font-weight:500">Deltagere :</b> Turneringen er åben for alle klubgolfere med gyldigt golfkort, gyldigt handicap og amatørstatus.</p>
      <h3>Hold og puljer</h3>
      <p>Et hold består af 2-4 spillere med to spillere fra holdet pr. match. Turneringen kører i puljer á 5-6 hold, som er delt op geografisk, efter hvor i landet I kommer fra. Puljens holdkaptajner aftaler selv indbyrdes tid og sted for den enkelte match - så I kan spille, hvor og hvornår det passer jer.<br>Alle betaler egen greenfee.</p>
      <h3>Spilleform</h3>
      <p>Spilleformen er en fourball - high/low hulspilsturnering, hvor 2 spillere fra holdet spiller med 2 spillere fra et andet hold.<br>Læs mere i turneringsbetingelserne, som du finder her på siden.</p>
      <h3>Stopdatoer</h3>
      <p>Runde 1: 18. maj<br>Runde 2: 8. juni<br>Runde 3: 29. juni<br>Runde 4: 17. august<br>Runde 5: 7. september</p>
      <h3>Finalestævne fredag den 18. september 2015</h3>
      <p>Vinderne fra hver pulje kvalificerer sig til at deltage i finalestævnet, som spilles på Egebjerg Golfklub, Skovbrynet 14, 5400 Egebjerg fredag den 18. september 2015 kl. 10.00.<br>Finalen bliver spillet som stableford four-ball best-ball med 7/8 handicap og med gunstart.<br>Finalestævnet spilles af to spillere fra hvert hold. Greenfee og middag betales af Nordlys Idrætsforbund.</p>
      <h3>Præmier</h3>
      <p>Puljevindernes præmie er deltagelse i finalestævnet.<br>Nordlys Idrætsforbund betaler greenfee, sportsbolle, vand og middag til finalestævnet.</p>
      <p style="margin-top:16px">Finalepræmier<br>1. præmie: Et rejsegavekort på op til kr. 22.000,- pr. hold, dog max. kr. 5.500,- pr. tilmeldt spiller.<br>2. præmie: Et gavekort til golfudstyr på kr. 2000,- pr. hold.<br>3. præmie: Et gavekort til golfudstyr på kr. 1000,- pr. hold.</p>
      <p>På finaledagen er der derudover præmie til længste drive og nærmest flaget.</p>
    </div>
  </main>
</div>
<footer class="footer">
  <div class="fbrand"><i></i><span>Nordlys<br>Idræts-<br>forbund</span></div>
  <div class="links">Om Nordlys Idrætsforbund &nbsp;|&nbsp; Bliv medlem &nbsp;|&nbsp; Magasinet NORDLYS &nbsp;|&nbsp; Find forening &nbsp;|&nbsp; Pressecenter &nbsp;|&nbsp; Find person &nbsp;|&nbsp; Min side</div>
  <div class="copyr">Copyright © 2015 Nordlys Idræt. All rights reserved.</div>
  <div class="soc"><i></i><i></i><i class="partner-round"></i></div>
</footer>
</body>
</html>
```